Business card, Invoice and printable service brochure

I need a 5.5x8.5 invoice, business card and printable service template for reception desk designed for my Rug repair, restoration and cleaning business.

I have included a picture for reference

www.velborenrug.example

Columns i need in my invoice:
Type of rug, Size, Background Color, Repair needs, Notes, Price and rug cleaning disclaimer.

Target Market(s)

Higher segment clients

Industry/Entity Type

Rug Repair, Restoration and cleaning,

Requirements
Must have
• Services hast to be listed on the invoice as well as service brochure.

```html
<!DOCTYPE html>
<html lang="en">
<head>
<meta charset="utf-8">
<title>Velboren Rug – Invoice and Business Card</title>
<link href="https://fonts.googleapis.com/css2?family=Libre+Baskerville:ital,wght@0,400;0,700;1,700&display=swap" rel="stylesheet">
<style>
  :root {
    --backdrop: #c5c6c4;
    --gold: #b39660;
    --dark: #1d1c1a;
    --ink: #2a2724;
    --paper: #ffffff;
    --rule-grey: #a7a7a7;
  }
  * { margin: 0; padding: 0; box-sizing: border-box; }
  html, body { width: 1200px; height: 1130px; overflow: hidden; }
  body {
    background: var(--backdrop);
    font-family: "Libre Baskerville", Georgia, serif;
    color: var(--ink);
    position: relative;
  }
  .abs { position: absolute; white-space: nowrap; }

  /* ---------- Invoice sheet ---------- */
  .invoice { position: absolute; left: 87px; top: 88px; width: 617px; height: 954px; background: var(--paper); }
  .invoice-header { position: absolute; left: 0; top: 0; width: 351px; height: 230px; }
  .frame { position: absolute; left: 0; top: 0; }
  .frame-1 { width: 351px; height: 230px; background: var(--gold); border-bottom-right-radius: 62px; }
  .frame-2 { width: 346px; height: 225px; background: var(--paper); border-bottom-right-radius: 57px; }
  .frame-3 { width: 341px; height: 220px; background: var(--gold); border-bottom-right-radius: 52px; }
  .frame-4 { width: 335px; height: 214px; background: var(--dark); border-bottom-right-radius: 46px; }

  .wordmark { font-weight: 400; color: var(--gold); letter-spacing: 0.5px; line-height: 1; }
  .tagline { color: var(--gold); line-height: 1; }

  .header-wordmark { left: 34px; top: 29px; font-size: 28px; }
  .header-tagline { left: 33px; top: 66px; font-size: 8.2px; letter-spacing: 3.6px; }

  .contact-list { position: absolute; left: 32px; top: 87px; list-style: none; }
  .contact-list li { display: flex; align-items: center; height: 15.5px; font-size: 10.6px; color: #f1ede6; }
  .contact-list svg { width: 8px; height: 8px; margin-right: 6px; flex: none; }
  .header-rule { position: absolute; left: 32px; top: 159px; width: 168px; height: 1px; background: var(--gold); }
  .hours { position: absolute; left: 46px; top: 164px; font-size: 10.6px; line-height: 15.6px; color: #f1ede6; }

  .doc-title { font-size: 19px; font-weight: 700; color: var(--gold); line-height: 1.2; }
  .field-list { font-size: 10.6px; line-height: 14.8px; }

  .table-head { position: absolute; left: 0; top: 240px; width: 617px; height: 38px; background: var(--gold); }
  .table-head span { position: absolute; top: 11px; transform: translateX(-50%); font-size: 13px; font-weight: 700; color: var(--ink); white-space: nowrap; }
  .table-head i { position: absolute; top: 0; width: 1px; height: 38px; background: var(--paper); }
  .grid { position: absolute; left: 0; top: 0; }

  .totals-label { font-size: 13px; font-weight: 700; line-height: 14px; }
  .payment-lines { font-size: 12px; line-height: 14px; }
  .total-bar { position: absolute; left: 393px; top: 751px; width: 203px; height: 38px; background: var(--gold); }
  .total-bar span { position: absolute; left: 9px; top: 12px; font-size: 13px; font-weight: 700; }

  .section-rule { position: absolute; height: 1px; }
  .note { left: 34px; top: 815px; width: 560px; font-size: 10.2px; line-height: 15px; white-space: normal; }

  .disclaimer-title { left: 34px; top: 862px; font-size: 8.6px; font-weight: 700; font-style: italic; line-height: 1; }
  .disclaimer { left: 34px; top: 874px; width: 561px; font-size: 7.35px; line-height: 10.5px; text-align: justify; white-space: normal; }

  /* ---------- Business card ---------- */
  .card { position: absolute; left: 734px; width: 399px; height: 223px; overflow: hidden; }
  .card-front { top: 358px; background: var(--dark); }
  .card-back { top: 653px; background: var(--paper); }
  .band { position: absolute; left: 0; width: 399px; }
  .front-wordmark { width: 399px; text-align: center; top: 424px; font-size: 27px; }
  .front-tagline { width: 399px; text-align: center; top: 458px; font-size: 7.4px; letter-spacing: 3.3px; }

  .card-name { left: 41px; top: 28px; font-size: 13px; letter-spacing: 0.2px; line-height: 1; }
  .card-name b { font-weight: 700; }
  .card-role { left: 41px; top: 44px; font-size: 10px; line-height: 1; }
  .card-contacts { position: absolute; left: 40px; top: 129px; list-style: none; }
  .card-contacts li { display: flex; align-items: center; height: 22px; font-size: 9px; }
  .card-contacts svg { width: 7px; height: 7px; margin-right: 9px; flex: none; }
  .card-divider { position: absolute; left: 232px; top: 131px; width: 1px; height: 92px; background: var(--gold); }
  .back-wordmark { left: 242px; top: 133px; font-size: 14.2px; letter-spacing: 0.2px; color: var(--ink); }
  .back-tagline { left: 242px; top: 151px; font-size: 4.2px; letter-spacing: 1.6px; color: var(--ink); }
  .back-hours { left: 242px; top: 169px; font-size: 9px; line-height: 12px; }
</style>
</head>
<body>

<!-- Invoice -->
<section class="invoice">
  <header class="invoice-header">
    <div class="frame frame-1"></div>
    <div class="frame frame-2"></div>
    <div class="frame frame-3"></div>
    <div class="frame frame-4"></div>

    <div class="abs wordmark header-wordmark">VELBOREN RUG</div>
    <div class="abs tagline header-tagline">REPAIR | RESTORATION | CLEANING</div>

    <ul class="contact-list">
      <li><svg viewBox="0 0 10 10"><path d="M5 0.5a3.2 3.2 0 0 0-3.2 3.2C1.8 6 5 9.5 5 9.5S8.2 6 8.2 3.7A3.2 3.2 0 0 0 5 0.5z" fill="none" stroke="#b39660" stroke-width="1.3"/><circle cx="5" cy="3.7" r="1.1" fill="#b39660"/></svg>4120 Marlow Ave, Brenton, IL 60199</li>
      <li><svg viewBox="0 0 10 10"><path d="M2.2 0.8l1.7 1.9-1 1.2c.6 1.4 1.8 2.6 3.2 3.2l1.2-1 1.9 1.7-1 1.6C4.5 9.2.8 5.5 1 1.8z" fill="none" stroke="#b39660" stroke-width="1.1"/></svg>(555)304-2718</li>
      <li><svg viewBox="0 0 10 10"><rect x="0.8" y="2" width="8.4" height="6.2" fill="none" stroke="#b39660" stroke-width="1.2"/><path d="M0.8 2L5 5.6 9.2 2" fill="none" stroke="#b39660" stroke-width="1.1"/></svg>info@velborenrug.example</li>
      <li><svg viewBox="0 0 10 10"><circle cx="5" cy="5" r="4.2" fill="none" stroke="#b39660" stroke-width="1"/><ellipse cx="5" cy="5" rx="1.8" ry="4.2" fill="none" stroke="#b39660" stroke-width="0.8"/><path d="M0.8 5h8.4M1.5 3h7M1.5 7h7" stroke="#b39660" stroke-width="0.7"/></svg>www.velborenrug.example</li>
    </ul>
    <div class="header-rule"></div>
    <div class="hours">Monday - Friday 9AM–5PM<br>Saturday 12PM–5PM<br>Sunday Closed</div>
  </header>

  <div class="abs doc-title" style="left:384px; top:40px;">Invoice</div>
  <div class="abs field-list" style="left:384px; top:68px;">Invoice NO.<br>Date:</div>
  <div class="abs doc-title" style="left:384px; top:117px;">Invoice to</div>
  <div class="abs field-list" style="left:384px; top:148px;">Client Name<br>Street Address Lane<br>Client City<br>Mobile</div>

  <div class="table-head">
    <span style="left:93px;">Type of Rug</span>
    <span style="left:249px;">Background Color</span>
    <span style="left:356px;">SIZE</span>
    <span style="left:438px;">PRICE</span>
    <span style="left:541px;">TOTAL</span>
    <i style="left:180px;"></i><i style="left:317px;"></i><i style="left:396px;"></i><i style="left:483px;"></i>
  </div>

  <svg class="grid" width="617" height="700" viewBox="0 0 617 700" aria-hidden="true">
    <g stroke="#b39660" stroke-width="1">
      <line x1="180.5" y1="283" x2="180.5" y2="686"/>
      <line x1="317.5" y1="283" x2="317.5" y2="686"/>
      <line x1="396.5" y1="283" x2="396.5" y2="686"/>
      <line x1="483.5" y1="283" x2="483.5" y2="686"/>
      <line x1="19" y1="334.5" x2="596" y2="334.5"/>
      <line x1="19" y1="393.5" x2="596" y2="393.5"/>
      <line x1="19" y1="453.5" x2="596" y2="453.5"/>
      <line x1="19" y1="513.5" x2="596" y2="513.5"/>
      <line x1="19" y1="572.5" x2="596" y2="572.5"/>
      <line x1="19" y1="632.5" x2="596" y2="632.5"/>
    </g>
  </svg>

  <div class="abs totals-label" style="left:34px; top:712px;">Payment Info:</div>
  <div class="abs payment-lines" style="left:34px; top:727px;">Account:<br>Bank Detail:</div>
  <div class="abs totals-label" style="left:402px; top:712px;">Sub Total:<br>Tax</div>
  <div class="total-bar"><span>Total</span></div>

  <div class="abs totals-label" style="left:33px; top:796px;">Repair Needs</div>
  <div class="section-rule" style="left:118px; top:806px; width:270px; background:var(--rule-grey);"></div>
  <p class="abs note"><b>NOTE</b> that in some instances, cleaning/treatment of carpets (due to the sudden rise in humidity) can trigger the alarm on Carbon Monoxide Detectors. There is no need for concern</p>

  <div class="abs disclaimer-title">RUG CLEANING DISCLAIMER.</div>
  <div class="section-rule" style="left:179px; top:868px; width:415px; background:var(--ink);"></div>
  <p class="abs disclaimer">According to our current policy with Velboren Rug we are not covered for work be carried out on carpets and upholstery only that which could be damaged near to it. However if we require all treatment cover we have to have a disclaimer notice in place. I want to make sure I,m covering every aspect. Areas like warning clients that the carpets will remian damp for a period of time and taking care when transfering from a damp area to say a tiled floor or vinyl covering where they can slip over. Recently heard of a case where cleaner had no disclaimer, cleaned carpets, owner came home, had a look at his work, went back into her hall which was mosaic tiles, slipped over because her shoes were wet and broke her wrists. He was sued for not warning her that this could happen.</p>
</section>

<!-- Business card front -->
<section class="card card-front">
  <div class="band" style="top:165px; height:6px; background:var(--gold);"></div>
  <div class="band" style="top:177px; height:6px; background:var(--gold);"></div>
</section>
<div class="abs wordmark front-wordmark" style="left:734px;">VELBOREN RUG</div>
<div class="abs tagline front-tagline" style="left:734px;">REPAIR | RESTORATION | CLEANING</div>

<!-- Business card back -->
<section class="card card-back">
  <div class="abs card-name"><b>ADRIAN</b> COLBERT</div>
  <div class="abs card-role">Director</div>

  <div class="band" style="top:80px; height:6px; background:var(--gold);"></div>
  <div class="band" style="top:86px; height:7px; background:var(--dark);"></div>
  <div class="band" style="top:93px; height:6px; background:var(--gold);"></div>

  <ul class="card-contacts">
    <li><svg viewBox="0 0 10 10"><path d="M5 0.5a3.2 3.2 0 0 0-3.2 3.2C1.8 6 5 9.5 5 9.5S8.2 6 8.2 3.7A3.2 3.2 0 0 0 5 0.5z" fill="none" stroke="#555" stroke-width="1.3"/><circle cx="5" cy="3.7" r="1.1" fill="#555"/></svg>4120 Marlow Ave, Brenton, IL 60199</li>
    <li><svg viewBox="0 0 10 10"><path d="M2.2 0.8l1.7 1.9-1 1.2c.6 1.4 1.8 2.6 3.2 3.2l1.2-1 1.9 1.7-1 1.6C4.5 9.2.8 5.5 1 1.8z" fill="none" stroke="#555" stroke-width="1.1"/></svg>(555)304-2718</li>
    <li><svg viewBox="0 0 10 10"><rect x="0.8" y="2" width="8.4" height="6.2" fill="none" stroke="#555" stroke-width="1.2"/><path d="M0.8 2L5 5.6 9.2 2" fill="none" stroke="#555" stroke-width="1.1"/></svg>info@velborenrug.example</li>
    <li><svg viewBox="0 0 10 10"><circle cx="5" cy="5" r="4.2" fill="none" stroke="#555" stroke-width="1"/><ellipse cx="5" cy="5" rx="1.8" ry="4.2" fill="none" stroke="#555" stroke-width="0.8"/><path d="M0.8 5h8.4M1.5 3h7M1.5 7h7" stroke="#555" stroke-width="0.7"/></svg>www.velborenrug.example</li>
  </ul>

  <div class="card-divider"></div>
  <div class="abs wordmark back-wordmark">VELBOREN RUG</div>
  <div class="abs tagline back-tagline">REPAIR | RESTORATION | CLEANING</div>
  <div class="abs back-hours">Monday - Friday 9AM–5PM<br>Saturday 12PM–5PM<br>Sunday Closed</div>
</section>

</body>
</html>
```